QVR business card

Need a business card for a company that provides instructional design and elearning development services. The website is here: http://quorvane.studio/

I'm attaching a current logo, as well as the old business card design. While I like to keep it clean, the old design is too simplistic for my liking. The only idea I want to reuse from the old design is placing industry jargon on the back of the card, just need a better way to present it. But if you have other ideas for the back--feel free to experiment.

Please use the colors complementary to the color we have on the website. Thank you!

```html
<!DOCTYPE html>
<html lang="en">
<head>
<meta charset="utf-8">
<title>QVR business card</title>
<link href="https://fonts.googleapis.com/css2?family=Open+Sans:wght@400;600&family=Encode+Sans+Condensed:wght@400&display=swap" rel="stylesheet">
<style>
  :root {
    --backdrop: #8f8f8f;
    --paper: #f4f4f2;
    --teal: #1fa6a2;
    --gold: #b7a86c;
    --ink: #4a4a4a;
    --rule: #9a9a9a;
    --back-text: #e9f0ef;
    --back-rule: #bfe3e1;
  }
  * { margin: 0; padding: 0; box-sizing: border-box; }
  html, body { width: 1105px; height: 1200px; overflow: hidden; }
  body { background: var(--backdrop); position: relative; font-family: "Open Sans", sans-serif; }

  .card { position: absolute; left: 182px; width: 746px; height: 426px; overflow: hidden; }
  .card--front { top: 119px; background: var(--paper); }
  .card--back { top: 637px; background: var(--teal); }

  .brand { position: absolute; left: 0; right: 0; top: 118px; display: flex; justify-content: center; align-items: center; gap: 16px; }
  .brand__mark { width: 44px; height: 44px; background: var(--teal); }
  .brand__name { font-weight: 600; font-size: 56px; line-height: 1; color: var(--teal); letter-spacing: 4px; }

  .holder { position: absolute; right: calc(746px - 315px); top: 252px; text-align: right; }
  .holder__name { font-size: 23px; color: var(--teal); line-height: 1.2; }
  .holder__role { font-size: 19px; color: var(--gold); line-height: 1.35; }

  .divider { position: absolute; left: 334px; top: 248px; width: 1px; height: 80px; background: var(--rule); }

  .contacts { position: absolute; left: 362px; top: 246px; list-style: none; }
  .contacts li { display: flex; align-items: center; gap: 10px; height: 29px; font-size: 17.5px; color: var(--ink); }
  .contacts svg { width: 17px; height: 17px; fill: var(--teal); flex: none; }

  .ask { position: absolute; left: 24px; top: 18px; color: var(--back-text); font-weight: 400; text-transform: uppercase; }
  .ask span { display: block; line-height: 1; }
  .ask .l1 { font-size: 82px; letter-spacing: 9px; margin-bottom: 12px; }
  .ask .l2 { font-size: 82px; letter-spacing: 9px; margin-bottom: 10px; }
  .ask .l3 { font-size: 112px; letter-spacing: 6px; margin-bottom: 8px; }
  .ask .l4 { font-size: 70px; letter-spacing: 5px; }

  .back-rule { position: absolute; left: 257px; top: 33px; width: 2px; height: 364px; background: var(--back-rule); }

  .jargon { position: absolute; left: 279px; top: 36px; width: 440px; list-style: none; font-family: "Encode Sans Condensed", sans-serif; color: var(--back-text); text-transform: uppercase; }
  .jargon li { font-size: 37px; line-height: 63.5px; text-align: justify; text-align-last: justify; white-space: nowrap; }
</style>
</head>
<body>
  <section class="card card--front">
    <div class="brand">
      <div class="brand__mark"></div>
      <div class="brand__name">QVR</div>
    </div>
    <div class="holder">
      <div class="holder__name">Marten Holloway</div>
      <div class="holder__role">CEO/Founder</div>
    </div>
    <div class="divider"></div>
    <ul class="contacts">
      <li><svg viewBox="0 0 24 24"><path d="M6.6 10.8a15.1 15.1 0 0 0 6.6 6.6l2.2-2.2c.3-.3.7-.4 1-.2 1.1.4 2.3.6 3.6.6.6 0 1 .4 1 1V20c0 .6-.4 1-1 1A17 17 0 0 1 3 4c0-.6.4-1 1-1h3.5c.6 0 1 .4 1 1 0 1.3.2 2.5.6 3.6.1.3 0 .7-.2 1z"/></svg>646-555-0187</li>
      <li><svg viewBox="0 0 24 24"><path d="M2 5h20v14H2z" fill="var(--teal)"/><path d="M3 6l9 7 9-7" fill="none" stroke="var(--paper)" stroke-width="1.6"/></svg>mholloway@quorvane.studio</li>
      <li><svg viewBox="0 0 24 24"><circle cx="12" cy="12" r="10"/><path d="M2 12h20M12 2c3 3 3 17 0 20M12 2c-3 3-3 17 0 20" fill="none" stroke="var(--paper)" stroke-width="1.4"/></svg>www.quorvane.studio</li>
    </ul>
  </section>

  <section class="card card--back">
    <h2 class="ask">
      <span class="l1">How</span>
      <span class="l2">Can</span>
      <span class="l3">We</span>
      <span class="l4">Help?</span>
    </h2>
    <div class="back-rule"></div>
    <ul class="jargon">
      <li>Mobile Learning SCORM</li>
      <li>Instructional Design LMS</li>
      <li>MOOCs eLearning HTML5</li>
      <li>Adult Learning Theory</li>
      <li>Gamification Classroom</li>
      <li>xAPI Blended Learning</li>
    </ul>
  </section>
</body>
</html>
```